LLC needs a business card design that emphasizes consulting and expert witness in upstream oil and g

I need a business card design for my company called Obena Consultative Service, LLC. My expertise is in oil and gas upstream operations management to optimize performance and also as an expert witness for law firms in oil and gas upstream operations litigation.
The final design should communicate knowledge and hands-on experience as well as trust. (Obena means rope or lasso. Perhaps "Obena" should be in the form of a rope.) I do not like the color green in any shade. My first preference would be some shade of blue.
Industry/Entity Type
Oil And Gas

```html
<!DOCTYPE html>
<html lang="en">
<head>
<meta charset="utf-8">
<title>Obena Consultative Service, LLC – Business Card</title>
<link rel="stylesheet" href="https://fonts.googleapis.com/css2?family=Alegreya:wght@400;700&family=Open+Sans:wght@700&display=swap">
<style>
  :root {
    --backdrop: #2b3032;
    --card: #070908;
    --white: #ffffff;
    --soft-white: #e8e8e8;
    --blue: #3aa4f0;
    --divider: #6a6d6c;
  }
  html, body {
    margin: 0;
    width: 1200px;
    height: 900px;
    overflow: hidden;
    background: var(--backdrop);
  }
  .canvas {
    position: relative;
    width: 1200px;
    height: 900px;
  }
  .card {
    position: absolute;
    left: 325px;
    width: 572px;
    height: 338px;
    background: var(--card);
  }
  .card--front { top: 96px; }
  .card--back { top: 483px; }

  .wordmark {
    position: absolute;
    display: flex;
    align-items: center;
    gap: 12px;
    font-family: "Alegreya", serif;
    font-weight: 700;
    color: var(--white);
    line-height: 1;
  }
  .wordmark__dot {
    background: var(--blue);
    border-radius: 50%;
  }
  .card--front .wordmark {
    left: 0; right: 0; top: 132px;
    justify-content: center;
    font-size: 84px;
  }
  .card--front .wordmark__dot { width: 22px; height: 22px; }

  .contact {
    position: absolute;
    right: 331px;
    top: 92px;
    text-align: right;
    font-family: "Alegreya", serif;
    color: var(--soft-white);
  }
  .contact__name {
    margin: 0;
    font-size: 25px;
    font-weight: 700;
    color: var(--white);
    line-height: 1;
  }
  .contact__role {
    margin: 4px 0 0;
    font-size: 16px;
    line-height: 1.2;
  }
  .contact__details {
    margin: 26px 0 0;
    font-size: 16px;
    line-height: 22px;
  }
  .contact__web {
    margin: 22px 0 0;
    font-size: 16px;
  }
  .divider {
    position: absolute;
    left: 266px;
    top: 87px;
    width: 1px;
    height: 176px;
    background: var(--divider);
  }
  .card--back .wordmark {
    left: 300px; top: 128px;
    font-size: 62px;
  }
  .card--back .wordmark__dot { width: 16px; height: 16px; }
  .tagline {
    position: absolute;
    left: 306px;
    top: 190px;
    margin: 0;
    font-family: "Open Sans", sans-serif;
    font-weight: 700;
    font-size: 14.5px;
    color: var(--white);
  }
</style>
</head>
<body>
<main class="canvas">
  <section class="card card--front" aria-label="Card front">
    <div class="wordmark"><span class="wordmark__dot"></span><span>Obena</span></div>
  </section>

  <section class="card card--back" aria-label="Card back">
    <div class="contact">
      <p class="contact__name">Daniel Hart</p>
      <p class="contact__role">Managing Director</p>
      <p class="contact__details">info@obenaconsult.com<br>555-284-0193</p>
      <p class="contact__web">www.obenaconsult.com</p>
    </div>
    <div class="divider"></div>
    <div class="wordmark"><span>Obena</span></div>
    <p class="tagline">Consultative Service, LLC</p>
  </section>
</main>
</body>
</html>
```